Process Serving Company needs a letterhead design

Looking to have a letterhead designed for letters to attorneys advertising our business. We would like something eye catching but professional. Colors and logos are attached. Please add "Process Service and Attorney Support" near the logo or header

Target Market(s)

Attorneys

Font styles to use
Serif
Sans Serif

Colors
33a6d7
0255a3
85cae6
cee9f5
ecf7fb

```html
<!DOCTYPE html>
<html lang="en">
<head>
<meta charset="utf-8">
<title>Mesa Ridge Serve – Letterhead</title>
<link rel="stylesheet" href="https://fonts.googleapis.com/css2?family=Open+Sans:wght@400;500&family=Roboto:wght@400&display=swap">
<style>
  :root{
    --brand:#33a6d7;
    --brand-deep:#0255a3;
    --brand-soft:#cee9f5;
    --ink:#555a5e;
    --ink-dark:#3f4347;
    --paper:#ffffff;
    --backdrop:#dcdcdc;
    --rule:#6b6f73;
  }
  *{margin:0;padding:0;box-sizing:border-box}
  html,body{width:1064px;height:1200px;overflow:hidden;background:var(--backdrop)}
  .letterhead{
    position:absolute;left:114px;top:29px;width:835px;height:1141px;
    background:var(--paper);
    font-family:"Open Sans",Arial,sans-serif;color:var(--ink);
  }
  .brand{
    position:absolute;left:0;right:0;top:86px;
    display:flex;justify-content:center;align-items:center;gap:14px;
  }
  .brand-mark{width:18px;height:18px;background:var(--brand)}
  .brand-text{display:flex;flex-direction:column;align-items:flex-start}
  .brand-name{
    font-weight:500;font-size:30px;line-height:1.1;color:var(--brand);letter-spacing:.5px;
  }
  .brand-tagline{
    font-family:"Roboto",Arial,sans-serif;font-size:8.5px;letter-spacing:.3px;
    color:var(--ink-dark);margin-top:4px;text-transform:uppercase;
  }
  .letter-body{
    position:absolute;left:75px;width:683px;top:265px;
    font-size:14.4px;line-height:22px;
  }
  .letter-body p{text-align:justify;margin-bottom:22px}
  .letter-body .greeting,.letter-body .closing{text-align:left}
  .signature{
    position:absolute;left:75px;top:844px;width:100px;height:91px;
    background:linear-gradient(135deg,#eeeeee,#e2e2e2);border-radius:4px;
  }
  .contact-bar{
    position:absolute;left:75px;right:75px;top:1022px;height:44px;
    font-family:"Roboto",Arial,sans-serif;font-size:16.5px;color:var(--ink-dark);
  }
  .contact-col{position:absolute;top:0;display:flex;flex-direction:column;gap:5px}
  .contact-col.phones{left:0}
  .contact-col.web{left:205px}
  .contact-col.address{left:490px;top:2px;gap:3px}
  .contact-line{display:flex;align-items:center;gap:7px;height:20px}
  .contact-line svg{width:16px;height:16px;fill:var(--brand);flex:none}
  .divider{position:absolute;top:2px;width:2px;height:40px;background:var(--rule)}
  .divider.first{left:169px}
  .divider.second{left:453px}
</style>
</head>
<body>
<main class="letterhead">
  <header class="brand">
    <span class="brand-mark"></span>
    <div class="brand-text">
      <span class="brand-name">Mesa Ridge Serve</span>
      <span class="brand-tagline">Process Service and Attorney Support</span>
    </div>
  </header>

  <section class="letter-body">
    <p class="greeting">Dear customer,</p>
    <p>Lorem ipsum dolor sit amet, consectetur adipisicing elit, sed do eiusmod tempor incididunt ut labore et dolore magna aliqua. Ut enim ad minim veniam, quis nostrud exercitation ullamco laboris nisi ut aliquip ex ea commodo consequat. Duis aute irure dolor in reprehenderit in voluptate velit esse cillum dolore eu fugiat nulla pariatur. Excepteur sint occaecat cupidatat non proident, sunt in culpa qui officia deserunt mollit anim id est laborum.</p>
    <p>Lorem ipsum dolor sit amet, consectetur adipisicing elit, sed do eiusmod tempor incididunt ut labore et dolore magna aliqua. Ut enim ad minim veniam, quis nostrud exercitation ullamco laboris nisi ut aliquip ex ea commodo consequat. Duis aute irure dolor in reprehenderit in voluptate velit esse cillum dolore eu fugiat nulla pariatur. Excepteur sint occaecat cupidatat non proident, sunt in culpa qui officia deserunt mollit anim id est laborum.</p>
    <p>Lorem ipsum dolor sit amet, consectetur adipisicing elit, sed do eiusmod tempor incididunt ut labore et dolore magna aliqua. Ut enim ad minim veniam, quis nostrud exercitation ullamco laboris nisi ut aliquip ex ea commodo consequat. Duis aute irure dolor in reprehenderit in voluptate velit esse cillum dolore eu fugiat nulla pariatur. Excepteur sint occaecat cupidatat non proident, sunt in culpa qui officia deserunt mollit anim id est laborum.</p>
    <p>Lorem ipsum dolor sit amet, consectetur adipisicing elit, sed do eiusmod tempor incididunt ut labore et dolore magna aliqua. Ut enim ad minim veniam, quis nostrud exercitation ullamco laboris nisi ut aliquip ex ea commodo consequat. Duis aute irure dolor in reprehenderit.</p>
    <p class="closing">Yours Sincerely,</p>
  </section>

  <div class="signature" role="img" aria-label="Handwritten signature of the sender"></div>

  <footer class="contact-bar">
    <div class="contact-col phones">
      <span class="contact-line">
        <svg viewBox="0 0 16 16" aria-hidden="true"><path d="M3.6 1.2l2.3 2.6-1.2 1.9c.9 2 2.6 3.7 4.6 4.6l1.9-1.2 2.6 2.3-1.4 2.6C7.2 13.6 2.4 8.8 1 3.6z"/></svg>
        480-555-0142
      </span>
      <span class="contact-line">
        <svg viewBox="0 0 16 16" aria-hidden="true"><path d="M4 1h8v4H4zM1 6h14v6h-3v3H4v-3H1zM5 10v3h6v-3z"/></svg>
        480-555-0187
      </span>
    </div>
    <span class="divider first"></span>
    <div class="contact-col web">
      <span class="contact-line">
        <svg viewBox="0 0 16 16" aria-hidden="true"><path d="M1 3h14v1.5L8 9 1 4.5zM1 6.3l7 4.4 7-4.4V13H1z"/></svg>
        Dana@MesaRidgeServe.com
      </span>
      <span class="contact-line">
        <svg viewBox="0 0 16 16" aria-hidden="true"><path d="M8 1a7 7 0 100 14A7 7 0 008 1zm0 1.5c.8 0 1.7 1.5 2 4H6c.3-2.5 1.2-4 2-4zM2.6 6.5h2.1a14 14 0 000 3H2.6a5.5 5.5 0 010-3zm3.5 0h3.8a12 12 0 010 3H6.1a12 12 0 010-3zm5.2 0h2.1a5.5 5.5 0 010 3h-2.1a14 14 0 000-3zM6 10.5h4c-.3 2.5-1.2 4-2 4s-1.7-1.5-2-4z"/></svg>
        www.MesaRidgeServe.com
      </span>
    </div>
    <span class="divider second"></span>
    <div class="contact-col address">
      <span>4120 E Canyon Rd STE 210</span>
      <span>Tempe AZ 85281</span>
    </div>
  </footer>
</main>
</body>
</html>
```